Maple Beacon Website

We are starting a marketing company and to do that we need a website! We want a website that will inspire and persuade to bring out the awesomeness in our clients.
What we want to see:
- Inspirational and persuasive imagery that relate to Branding.
- No cliche images eg. business man, suits and hand shakes
- We want to transform and educate our clients.
- We want to show them the path and would like our website to really act as a guide that guides them step by step through our process.
- We want the portray that we are an investment but not have a pretentious way to it. We put our heart into every project and that is how we treat our clients.
-When you submit your design please include what platform you have created for. Preference would be Wordpress or Joobla.

We have included the psd file for the wire frame, logo files, font files, site map and a link to a video we create to give you more information on what we would like to see. http://clipvault.example/t/qk82LmZpr

Feel free to make small modification to the logos if you think it will improve it. Your creativity and advice is most welcome.
Updates

One thing we forgot. We would like to have our contact information near the top of the website as well as at the bottom.  Here is out contact info:

Email: info@maplebeacon.example
Phone: 587-555-0142

Project Deadline Extended
Reason: As we are new with the platform and that we want to optimize our results, we decided to extend the deadline by 15 days. Thanks!

Target Market(s)

28-60, Male and Female, Oil field, Local Businesses, Dentists, Chiropractors, Hair salon, Construction/Renovation, Events etc

Industry/Entity Type

Investment

Requirements
Must have
• - 4 Inspirational and persuasive Imagery for the top portion of the website
- Must have a feel as if your not on a website an example of this is linked below.
http://www.artbidhub.example/design/402957/web-design-by-lena-torvik
Nice to have
• - Creative advice from you.
- Creative buttons for Get Free Quote and Subscribe buttons. Something out of the box that draws peoples attention. eg. a 'B' button. Just and example but still something related to branding.
Should not have
• No Cliches

```html
<!DOCTYPE html>
<html lang="en">
<head>
<meta charset="utf-8">
<title>Maple Beacon</title>
<link rel="stylesheet" href="https://fonts.googleapis.com/css2?family=Signika:wght@400;600;700&family=Cabin:ital,wght@0,400;0,600;0,700;1,600&display=swap">
<style>
:root{
  --bar:#4a4a4a;
  --white:#ffffff;
  --page:#f7f7f7;
  --panel:#f4f4f4;
  --panel-line:#e9e9e9;
  --strip:#d8d8d8;
  --nav-green:#8dc63f;
  --menu-green:#6b8a4c;
  --head-green:#4f6e27;
  --lead-green:#8cb536;
  --btn-top:#b5d553;
  --btn-bottom:#8fb834;
  --btn-edge:#6f9222;
  --callout:#55c94a;
  --ink:#444444;
  --body:#555555;
  --soft:#cfcfcf;
}
*{box-sizing:border-box;margin:0;padding:0}
html,body{width:1200px;height:981px;overflow:hidden}
body{position:relative;background:var(--page);font-family:"Cabin",sans-serif;color:var(--body)}
.abs{position:absolute}

/* top navigation */
.top-bar{left:0;top:0;width:1200px;height:50px;background:var(--bar)}
.top-nav a{position:absolute;top:13px;font-family:"Signika",sans-serif;font-weight:700;font-size:19px;color:var(--white);text-decoration:none;letter-spacing:.2px}
.top-nav a.is-current{color:var(--nav-green)}

/* hero */
.hero{left:0;top:50px;width:1200px;height:356px;background:var(--white)}
.brand{left:140px;top:64px;display:flex;align-items:center;gap:8px}
.brand-dot{width:18px;height:18px;border-radius:50%;background:var(--ink)}
.brand-name{font-family:"Signika",sans-serif;font-weight:700;font-size:34px;color:var(--ink);line-height:1}
.tagline{left:170px;top:125px;font-family:"Cabin",sans-serif;font-style:italic;font-weight:600;font-size:14px;color:var(--ink)}
.side-menu a{position:absolute;left:130px;height:29px;background:var(--menu-green);color:var(--white);font-family:"Signika",sans-serif;font-weight:700;font-size:14px;letter-spacing:.5px;line-height:29px;padding-left:22px;text-decoration:none}
.hero-art{left:300px;top:62px;width:770px;height:340px;background:linear-gradient(100deg,#f9e4ef 0%,#fdf3df 22%,#e4f0fb 45%,#eeeeee 62%,#fde6d6 82%,#fff6c9 100%)}
.callout{left:757px;top:272px;width:313px;height:130px;background:var(--callout);color:var(--white);padding:16px 0 0 16px}
.callout h2{font-family:"Cabin",sans-serif;font-weight:700;font-size:23px;line-height:25px}
.callout p{margin-top:9px;font-weight:700;font-size:16px;line-height:16px}
.callout svg{vertical-align:-1px;margin-left:4px}
.hero-rule{left:129px;top:402px;width:941px;height:4px;background:#222}

/* strips */
.strip{background:var(--strip);background-image:repeating-linear-gradient(45deg,rgba(255,255,255,.18) 0 1px,transparent 1px 3px)}
.strip::after{content:"";position:absolute;left:4%;right:4%;bottom:-12px;height:12px;border-radius:50%;background:radial-gradient(ellipse at top,rgba(0,0,0,.18),transparent 70%)}
.connect{left:130px;top:422px;width:220px;height:98px}
.strip-title{font-family:"Signika",sans-serif;font-weight:700;font-size:19px;color:var(--ink);text-align:center;margin-top:13px;letter-spacing:.3px}
.strip-title em{font-style:normal;color:var(--head-green)}
.social{position:absolute;top:50px;width:30px;height:30px;border-radius:4px}
.newsletter{left:371px;top:422px;width:699px;height:98px}
.field{left:82px;top:49px;width:405px;height:34px;border-radius:5px;background:var(--white);border:1px solid #c4c4c4;box-shadow:inset 0 2px 3px rgba(0,0,0,.12)}
.btn{display:block;background:linear-gradient(var(--btn-top),var(--btn-bottom));border:1px solid var(--btn-edge);border-radius:3px;color:var(--white);text-align:center;text-decoration:none;font-family:"Cabin",sans-serif;font-weight:700;text-shadow:0 1px 1px rgba(0,0,0,.35)}
.btn-subscribe{left:496px;top:49px;width:123px;height:34px;line-height:32px;font-family:"Signika",sans-serif;font-size:16px;letter-spacing:.5px}

/* content panels */
.panel{background:var(--panel);border:3px solid var(--panel-line)}
.welcome{left:130px;top:554px;width:620px;height:320px;padding:14px 21px 0}
.panel h1,.panel h3{font-family:"Signika",sans-serif;font-weight:700;font-size:23px;color:var(--head-green)}
.lead{margin-top:10px;font-weight:700;font-size:14px;line-height:20px;color:var(--lead-green)}
.body-copy{margin-top:8px;font-size:13px;line-height:23px;color:var(--body)}
.btn-read{left:21px;top:262px;width:101px;height:29px;line-height:27px;font-size:14px}
.quote{left:770px;top:554px;width:300px;height:320px;text-align:center;padding-top:20px}
.quote p{margin:18px auto 0;width:260px;font-size:14px;line-height:24px;color:var(--body)}
.btn-quote{left:41px;top:198px;width:212px;height:48px;line-height:46px;font-size:18px}

/* footer */
.footer{left:0;top:892px;width:1200px;height:89px;background:var(--bar);text-align:center}
.footer-nav{margin-top:25px;font-size:11px;color:var(--white);letter-spacing:.3px}
.footer-nav a{color:var(--white);text-decoration:none;text-transform:uppercase}
.footer-nav span{margin:0 12px}
.copyright{margin-top:11px;font-size:10px;color:var(--soft);letter-spacing:.3px}
</style>
</head>
<body>

<header class="abs top-bar">
  <nav class="top-nav">
    <a href="#" class="is-current" style="left:418px">Maple Beacon</a>
    <a href="#" style="left:618px">Be Found</a>
    <a href="#" style="left:803px">Connect</a>
    <a href="#" style="left:962px">Get Growing</a>
  </nav>
</header>

<section class="abs hero"></section>
<div class="abs hero-art" role="img" aria-label="Illustration of a person connected to social network bubbles, linking through dotted paths to a central Brand circle and a group of friends"></div>

<div class="abs brand">
  <span class="brand-dot"></span>
  <span class="brand-name">Maple Beacon</span>
</div>
<div class="abs tagline">Because You're Awesome!</div>

<nav class="side-menu">
  <a href="#" style="top:157px;width:114px">STRATEGY</a>
  <a href="#" style="top:206px;width:125px">PORTFOLIO</a>
  <a href="#" style="top:256px;width:106px">ABOUT US</a>
  <a href="#" style="top:306px;width:127px">CONTACT US</a>
  <a href="#" style="top:356px;width:80px">BLOG</a>
</nav>

<aside class="abs callout">
  <h2>What's the upside of<br>being 'social'?</h2>
  <p>Speak to one of our<br>communications strategists now<svg width="9" height="13" viewBox="0 0 9 13"><path d="M2 1.5l5 5-5 5" fill="none" stroke="#fff" stroke-width="2.4"/></svg></p>
</aside>
<div class="abs hero-rule"></div>

<section class="abs strip connect">
  <h4 class="strip-title">CONNECT WITH US</h4>
  <span class="social" style="left:17px;background:#3b5b9a"></span>
  <span class="social" style="left:56px;background:#5bbde6"></span>
  <span class="social" style="left:96px;background:#1d6fa5"></span>
  <span class="social" style="left:135px;background:#f07a16"></span>
  <span class="social" style="left:174px;background:#c4221c"></span>
</section>

<section class="abs strip newsletter">
  <h4 class="strip-title">GET TIPS AND TRICKS! <em>SUBSCRIBE TO OUR NEWSLETTER</em></h4>
  <div class="abs field"></div>
  <a href="#" class="abs btn btn-subscribe">SUBSCRIBE</a>
</section>

<article class="abs panel welcome">
  <h1>Welcome to Our Site</h1>
  <p class="lead">Lorem ipsum dolor sit amet, consectetur adipiscing elit. Fusce accumsan, elit a suscipit sagittis, tortor sapien cursus risus, non rhoncus lectus nunc ac nulla..</p>
  <p class="body-copy">Aliquam molestie, mi et imperdiet euismod, dui purus auctor tellus, et interdum lacus lectus et ante. Sed accumsan sollicitudin sapien, sit amet adipiscing turpis gravida ac. In congue, neque ac lobortis volutpat, libero mauris varius mi, vitae suscipit ipsum ligula vitae risus. Duis aliquam nibh a dui iaculis viverra id a velit. Vivamus egestas risus in magna varius commodo. Sed semper viverra egestas. Etiam pretium porttitor lectus, vel ornare neque porta volutpat. Aenean a nibh eget turpis vehicula tempus ac sed massa.</p>
  <a href="#" class="abs btn btn-read">Read More</a>
</article>

<aside class="abs panel quote">
  <h3>Get a Free Quote</h3>
  <p>If you would like to more information on how we can help you achive your goals. You can visit our strategy page or simply get a free Quote !</p>
  <a href="#" class="abs btn btn-quote">GET A FREE QUOTE</a>
</aside>

<footer class="abs footer">
  <div class="footer-nav">
    <a href="#">Strategy</a><span>|</span><a href="#">Portfolio</a><span>|</span><a href="#">About Us</a><span>|</span><a href="#">Contact Us</a><span>|</span><a href="#">Blog</a><span>|</span><a href="#">Site Map</a>
  </div>
  <div class="copyright">COPYRIGHT ©2013. MAPLE BEACON INC. | ALL RIGHT RESERVED</div>
</footer>

</body>
</html>
```